Breakfast Cafe - The Sunny Nook

It is for my breakfast and lunch cafe with a hawaiian / beach theme. I am open 7 days a week from 7am to 2pm. We serve traditional American food such as omelettes, pancakes, burgers and sandwiches. I'll upload my old card and my new logo to be used. We have a lot of day to day regulars who eat there during the week, our t-shirts actually say 'Locals Only' on them. Hope this helps. Thanks.

Target Market(s)

anyone who has an appetite!

Industry/Entity Type

American Restaurant

Contact Information for Business Card

4815C Marlow Grove Avenue
Long Beach, California
(555) 731-2294

Requirements
Must have
• Address and phone number easily readable.
Nice to have
• beach or tropical theme

```html
<!DOCTYPE html>
<html lang="en">
<head>
<meta charset="utf-8">
<title>The Sunny Nook – Business Card</title>
<link rel="stylesheet" href="https://fonts.googleapis.com/css2?family=Exo+2:wght@700&family=Oswald:wght@500;600&display=swap">
<style>
  :root {
    --page-bg: #e4e4e2;
    --sun-orange: #f7a43a;
    --sun-yellow: #ffd52e;
    --ray-yellow: #ffe14a;
    --night: #1c1c1e;
    --surf-blue: #4fc0e3;
    --name-blue: #8fd6ee;
    --emblem-brown: #8a5a2c;
    --tag-orange: #c97a2f;
    --headline-orange: #f6a13b;
    --ink: #111111;
  }
  html, body {
    margin: 0;
    width: 1200px;
    height: 960px;
    overflow: hidden;
    background: var(--page-bg);
  }
  .card {
    position: absolute;
    left: 110px;
    top: 200px;
    width: 980px;
    height: 560px;
    display: block;
  }
  .rays line { stroke: var(--ray-yellow); stroke-width: 7; stroke-linecap: round; }
  .contact { font-family: "Exo 2", sans-serif; font-weight: 700; fill: var(--ink); text-anchor: middle; }
  .contact-address { font-size: 18px; }
  .contact-phone { font-size: 26px; }
  .brand-name { font-family: "Oswald", sans-serif; font-weight: 600; font-size: 36px; fill: var(--name-blue); text-anchor: middle; }
  .brand-place { font-family: "Oswald", sans-serif; font-weight: 500; font-size: 11px; letter-spacing: 3px; fill: var(--tag-orange); text-anchor: middle; }
  .headline { font-family: "Oswald", sans-serif; font-weight: 600; font-size: 31px; letter-spacing: 1.5px; fill: var(--headline-orange); text-anchor: middle; }
  .hours { font-family: "Oswald", sans-serif; font-weight: 500; font-size: 14px; fill: var(--surf-blue); text-anchor: middle; }
  .hours-rule { stroke: var(--headline-orange); stroke-width: 1.5; }
</style>
</head>
<body>
<svg class="card" viewBox="0 0 700 400" xmlns="http://www.w3.org/2000/svg">
  <defs>
    <clipPath id="card-edge"><rect width="700" height="400"/></clipPath>
  </defs>
  <g clip-path="url(#card-edge)">
    <rect class="sky" width="700" height="400" fill="var(--sun-orange)"/>
    <g class="rays">
      <line x1="414" y1="212" x2="-156" y2="59"/>
      <line x1="425" y1="185" x2="-86" y2="-110"/>
      <line x1="442" y1="162" x2="25" y2="-255"/>
      <line x1="465" y1="145" x2="170" y2="-366"/>
      <line x1="492" y1="134" x2="339" y2="-436"/>
      <line x1="520" y1="130" x2="520" y2="-460"/>
      <line x1="548" y1="134" x2="701" y2="-436"/>
      <line x1="575" y1="145" x2="870" y2="-366"/>
      <line x1="598" y1="162" x2="1015" y2="-255"/>
      <line x1="615" y1="185" x2="1126" y2="-110"/>
      <line x1="626" y1="212" x2="1196" y2="59"/>
    </g>
    <circle class="sun" cx="520" cy="240" r="112" fill="var(--sun-yellow)"/>
    <path class="surf-line" d="M360,206 C430,232 470,240 520,233 C600,223 660,176 700,144" fill="none" stroke="var(--surf-blue)" stroke-width="9"/>
    <path class="night-wave" d="M0,185 C90,150 200,128 280,168 C340,198 420,240 520,230 C600,220 660,176 700,150 L700,400 L0,400 Z" fill="var(--night)"/>

    <circle class="brand-emblem" cx="196" cy="170" r="112" fill="var(--emblem-brown)" role="img" aria-label="Cafe emblem: tropical beach scene"/>
    <text class="brand-name" x="196" y="310">The Sunny Nook</text>
    <text class="brand-place" x="196" y="348">LONG BEACH, CA</text>

    <text class="contact contact-address" x="502" y="70">4815C Marlow Grove</text>
    <text class="contact contact-address" x="502" y="92">Avenue Long Beach</text>
    <text class="contact contact-address" x="502" y="114">California</text>
    <text class="contact contact-phone" x="502" y="158">(555) 731-2294</text>

    <text class="headline" x="508" y="287">BREAKFAST &amp;</text>
    <text class="headline" x="508" y="321">LUNCH CAFE</text>
    <text class="hours" x="508" y="343">OPEN 7 DAYS A WEEK FROM</text>
    <line class="hours-rule" x1="392" y1="351" x2="624" y2="351"/>
    <text class="hours" x="508" y="370">7AM TO 2PM.</text>
  </g>
</svg>
</body>
</html>
```